K&T Smokehouse Website Design Project

K& T Smokehouse AsaderÃa is a fast-casual restaurant that specializes in southern culture, soul food, baby back ribs and bourbon whiskey.
We need a functional and user friendly website design for our customers to be able to explore our menu options, learn about our culture, as well as be able to place and pay for online orders that can be picked up at the nearest restaurant. Benchmarks for our website are www.crumbvalebakery.com, www.zestoragrill.com and www.marisolkitchen.com
The site design should also serve as an initial point of contact for prospective franchisees to dig and learn about the brand and business opportunity.
We want customers (consumers and potential franchisees) to be able to experience FIRST THE FOOD, but also the style and culture of our restaurants via the website design. Key elements for this are: soul food (Warm Your Heart), southern culture, friendly service, bluegrass/folk music, bourbon/moonshine/Tennessee whisky, modern butcher-shop design as well as industrial, wood, modern rustic, organic elements. (see restaurant images of tile, concrete, vintage scales, green wall, etc)
We want the website to provide a good overall brand image and also drive participation and sales by via images of our food, by these images being at front and center of the website design. See benchmark websites (Crumbvale, Marisol Kitchen, Zestora) for good examples of this.
Other elements to take under consideration for the website design are:
* Illustrative but simple menu
* Hacer un pedido (order online), Loyalty Program and Franquicias sections should have different, separate and easy to see buttons in the homepage.
* Simple, but modern functionality overall for the website.
* Respect colors and elements of the brand (attached some photos and examples)
* Brand Typography included (NAMES OF TYPOGRAPHY: BEBAS, SONGBIRD, CANTER & VAST SHADOW)
Minimum Deliverables: Home Page, Menu and Order Online. 3 pages total.
• More examples can be found at: www.facebook.com/ktsmokehouseasaderia
• Website architecture / Site Map ATTACHED
* More design elements attached.
* Screenshots of some good elements to take under consideration for website functionality and design.
- BEBAS, SONGBRID, CANTER & VAST SHADOW

```html
<!DOCTYPE html>
<html lang="es">
<head>
<meta charset="utf-8">
<title>K&amp;T Smokehouse Asaderia</title>
<link href="https://fonts.googleapis.com/css2?family=Alegreya+SC:wght@700&family=PT+Sans:wght@400;700&family=Open+Sans:wght@400&display=swap" rel="stylesheet">
<style>
:root{
  --brand:#8a0c15;
  --brand-dark:#6e0710;
  --ink:#222;
  --muted:#777;
  --light:#f4f4f4;
  --footer:#1d1d1d;
  --footer-base:#151515;
  --footer-text:#a8a8a8;
}
*{margin:0;padding:0;box-sizing:border-box}
html,body{width:859px;height:1200px;overflow:hidden}
body{position:relative;font-family:"PT Sans",sans-serif;color:var(--ink);background:#fff}
.abs{position:absolute}
.topbar{left:0;top:0;width:859px;height:30px;background:linear-gradient(#9a1019,var(--brand-dark));color:#fff;font-size:12px}
.topbar span{position:absolute;top:8px;display:flex;align-items:center;gap:8px}
.header{left:0;top:30px;width:859px;height:71px;background:#fff}
.brand{position:absolute;left:64px;top:13px;display:flex;align-items:center;gap:6px;font-weight:700;font-size:13px;color:#111}
.brand i{width:14px;height:14px;border-radius:50%;background:var(--brand);display:block}
.nav{position:absolute;right:70px;top:28px;display:flex;gap:34px;font-size:12px}
.hero{left:0;top:101px;width:859px;height:423px;background:radial-gradient(ellipse at 55% 45%,#7a2a26 0%,#5a1e1c 45%,#7a5a44 80%,#8d7360 100%)}
.hero-title{left:0;width:859px;top:234px;text-align:center;font-family:"Alegreya SC",serif;font-size:31px;color:#fff;letter-spacing:.5px}
.hero-sub{left:0;width:859px;top:270px;text-align:center;color:#fff;font-size:23px;line-height:32px}
.btn{top:353px;height:29px;background:#fff;color:var(--brand);font-size:13px;display:flex;align-items:center;justify-content:center;gap:12px;border-radius:2px;box-shadow:0 2px 0 #ccc}
.arrow{top:292px;color:#fff;font-size:30px;opacity:.7}
.features{left:63px;top:487px;width:733px;height:168px;display:flex;box-shadow:0 2px 6px rgba(0,0,0,.3)}
.feature{flex:1;position:relative}
.feature .cap{position:absolute;left:16px;right:16px;top:34px;height:100px;background:rgba(60,40,30,.55);color:#fff;text-align:center}
.feature h3{font-size:15px;margin-top:20px}
.feature p{font-size:11.5px;margin-top:6px}
.feature .link{font-size:12px;margin-top:4px}
.welcome h2{font-family:"Open Sans",sans-serif;font-weight:400;font-size:21px}
.welcome{left:0;top:684px;width:859px;text-align:center}
.welcome hr{width:362px;margin:6px auto 13px;border:0;border-top:1px solid #e2e2e2}
.welcome p{font-family:"Open Sans",sans-serif;font-size:9.5px;color:var(--muted);line-height:16px;width:610px;margin:0 auto}
.menu-sec{left:0;top:784px;width:859px;height:222px;background:var(--light)}
.menu-sec h2{text-align:center;font-family:"Open Sans",sans-serif;font-weight:400;font-size:21px;margin-top:30px}
.card{top:851px;width:175px;height:117px;background:#fff;box-shadow:0 1px 2px rgba(0,0,0,.15)}
.card .img{height:92px;position:relative}
.card .img .t{position:absolute;left:9px;top:20px;color:#fff;font-size:13px}
.card .img .d{position:absolute;left:9px;top:40px;right:8px;color:#fff;font-size:8px;line-height:12px}
.card .acts{display:flex;height:25px;font-size:9.5px}
.card .acts span{flex:1;display:flex;align-items:center;justify-content:center;gap:5px}
.card .det{background:var(--brand);color:#fff}
.card .view{color:var(--brand)}
.footer{left:0;top:1006px;width:859px;height:144px;background:var(--footer);color:var(--footer-text);font-size:9.5px}
.fcol{position:absolute;top:20px;list-style:none}
.fcol li{height:20px;display:flex;align-items:center;gap:10px}
.fcol li::before{content:"";width:9px;height:9px;border:1px solid #bbb;border-radius:50%;display:block}
.contact{position:absolute;left:658px;top:19px;line-height:20px}
.contact .w{color:#eee}
.social{display:flex;gap:9px;margin-top:5px}
.social i{width:10px;height:10px;border-radius:50%;background:#eee;display:block}
.base{left:0;top:1150px;width:859px;height:50px;background:var(--footer-base);color:#ddd;font-size:7.5px}
.base span{position:absolute;top:23px}
</style>
</head>
<body>
<div class="abs topbar">
  <span style="left:64px"><svg width="10" height="10" viewBox="0 0 10 10"><path d="M2 0l2 2-1 2c1 1 2 2 3 3l2-1 2 2-2 2C4 10 0 6 0 2z" fill="#fff"/></svg>555 204 7719</span>
  <span style="left:193px"><svg width="11" height="9" viewBox="0 0 11 9"><rect width="11" height="9" fill="#fff"/><path d="M0 0l5.5 5L11 0" stroke="#8a0c15" fill="none"/></svg>ventas@ktsmokehouse.com</span>
  <span style="left:726px"><svg width="9" height="10" viewBox="0 0 9 10"><circle cx="4.5" cy="3" r="2.6" fill="#fff"/><path d="M0 10c0-3 2-4.5 4.5-4.5S9 7 9 10z" fill="#fff"/></svg>Log in</span>
</div>
<header class="abs header">
  <div class="brand" style="top:27px"><i></i>K&amp;T Smokehouse</div>
  <nav class="nav"><span>Home</span><span>Nosotros</span><span>Menu</span><span>Promocion</span><span>Ubicacion</span></nav>
</header>
<div class="abs hero" role="img" aria-label="Close-up photo of glazed baby back ribs being brushed with barbecue sauce on a wooden board"></div>
<div class="abs hero-title">K&amp;T SMOKEHOUSE ASADERIA</div>
<div class="abs hero-sub">Fusce euismod consequat anteelit sed dolor.<br>Aliquam congue fermentum nisl.</div>
<div class="abs arrow" style="left:62px">&#8249;</div>
<div class="abs arrow" style="left:786px">&#8250;</div>
<div class="abs btn" style="left:287px;width:117px">Order Online <span>&#10230;</span></div>
<div class="abs btn" style="left:442px;width:130px">Order Catering <span>&#10230;</span></div>
<div class="abs features">
  <div class="feature" role="img" aria-label="Photo of smoked ribs on paper" style="background:linear-gradient(135deg,#c9a28a,#7a3028 50%,#b78c74)"><div class="cap"><h3>Nuestras Costillitas</h3><p>Estilo baby back con sabor autentico!</p><div class="link">&#128279;</div></div></div>
  <div class="feature" role="img" aria-label="Photo of french fries" style="background:linear-gradient(135deg,#d9c08f,#a07a46 50%,#e0cfa8)"><div class="cap"><h3>Papas a la Francesa</h3><p>Nam libero tempore, cum soluta</p><div class="link">&#128279;</div></div></div>
  <div class="feature" role="img" aria-label="Photo of organic green salad" style="background:linear-gradient(135deg,#b3a58e,#3d5a2a 50%,#8b7a6a)"><div class="cap"><h3>Ensalada Organica</h3><p>Nam libero tempore, cum soluta</p><div class="link">&#128279;</div></div></div>
</div>
<section class="abs welcome">
  <h2>Welcome</h2><hr>
  <p>Lorem ipsum dolor sit amet conse ctetur adipisicing elit, sed do eiusmod tempor in cidi dunt ut labore et dolore magna aliqua. Ut enim ad minim veniam, quis nostrud ex ercita tion ullamco laboris nisi ut aliquip ex ea commod</p>
</section>
<section class="abs menu-sec"><h2>Our Menu</h2></section>
<div class="abs card" style="left:64px"><div class="img" role="img" aria-label="Photo of ribs with red overlay" style="background:linear-gradient(135deg,#b54a44,#8c1f1e)"><div class="t">Temporibus autem</div><div class="d">Lorem Ipsum is simply dummy text of the printing and typesetting industry.</div></div><div class="acts"><span class="det">&#9906; Details</span><span class="view">&#128279; View online</span></div></div>
<div class="abs card" style="left:250px"><div class="img" role="img" aria-label="Photo of glazed rib close-up" style="background:linear-gradient(135deg,#5a2418,#a5442a 55%,#e8e0d8)"></div><div class="acts"><span class="det">&#9906; Details</span><span class="view">&#128279; View online</span></div></div>
<div class="abs card" style="left:436px"><div class="img" role="img" aria-label="Photo of a rack of smoked ribs" style="background:linear-gradient(180deg,#3a1c14,#7a3a26 50%,#4a2418)"></div><div class="acts"><span class="det">&#9906; Details</span><span class="view">&#128279; View online</span></div></div>
<div class="abs card" style="left:621px"><div class="img" role="img" aria-label="Photo of sweet potato fries in a paper basket" style="background:radial-gradient(circle at 45% 55%,#e07a22,#8a6a4a 50%,#d8d0c4)"></div><div class="acts"><span class="det">&#9906; Details</span><span class="view">&#128279; View online</span></div></div>
<footer class="abs footer">
  <ul class="fcol" style="left:64px"><li>FAQs Page</li><li>Hot Offers</li><li>Newsletter Sign Up</li></ul>
  <ul class="fcol" style="left:275px"><li>Special Offers</li><li>Useful Links</li><li>Photo Gallery</li><li>Menu</li></ul>
  <ul class="fcol" style="left:469px"><li>Testimonials</li><li>Our Staff</li><li>Resources</li><li>Contact Us</li><li>Forum</li></ul>
  <div class="contact">
    <div class="w">SERVICIO A DOMICILIO</div>
    <div>555 204 7719</div>
    <div>Email: ventas@ktsmokehouse.com</div>
    <div class="w">24/7 Dedicated Customer Support</div>
    <div>Follow Us!</div>
    <div class="social"><i></i><i></i><i></i><i></i><i></i></div>
  </div>
</footer>
<div class="abs base"><span style="left:64px">COPYRIGHTS© 2014 K&amp;T SMOKEHOUSE ASADERIA• PRIVACY POLICY</span><span style="left:826px">C13</span></div>
</body>
</html>
```